Field Anchor - Design a new page for our website

The designer is to use our existing website to match color and style and the documents provided to create a webpage that reflects the information in the brochure attached. This should also include a button to download our brochure and a form to request more information by entering name, phone, and email. This page will be added to our main site and will be coded by our webmaster team.

View website at www.harrowfield.us

The successful designer will be asked to also design another page for additional compensation.

Target Market(s)

Security and Law Enforcement

Industry/Entity Type

Security Service

Coding

Number of Pages Required

1 page

Font styles to use
Other font styles liked:
• Raleway or match site font and style

Requirements
Must have
• Match in color and style to our existing site as this page will be added to the existing website.

UPDATE: Place FRB Logo (attached to the brief) in a horizontal bar the width of the page with the following text:

"Field Anchor and all of Harrowfield's services are available on under our FRB Contract." (Add button) Click for Info
Nice to have
• Simple design expressing clean and easy to comprehend points

Please be creative, use the ability to scroll vertically on the page to space out the content and add supporting graphics or images.

```html
<!DOCTYPE html>
<html lang="en">
<head>
<meta charset="utf-8">
<title>Field Anchor – Special Event Services</title>
<link href="https://fonts.googleapis.com/css2?family=Raleway:wght@400;500;600;700&display=swap" rel="stylesheet">
<style>
:root{
  --navy:#22467f;
  --blue:#1a9ad6;
  --red:#e3232b;
  --black:#060606;
  --ink:#2a2a2a;
  --muted:#8a8a8a;
  --yellow:#f4e21b;
  --stage:#ffffff;
  --field:#8fb0d8;
}
*{box-sizing:border-box;margin:0;padding:0}
html,body{width:1200px;height:1200px;overflow:hidden;background:var(--stage);font-family:'Raleway',sans-serif;color:var(--ink)}
.page{position:absolute;left:463px;top:0;width:274px;height:1200px;background:#fff;box-shadow:0 0 10px rgba(0,0,0,.35);overflow:hidden}
.abs{position:absolute}
/* nav */
.site-nav{left:0;top:0;width:274px;height:14px;background:var(--navy)}
.brand{left:18px;top:2.5px;display:flex;align-items:center;gap:2px;color:#fff;font-weight:700;font-size:6.5px;letter-spacing:.1px}
.brand-dot{width:5px;height:5px;border-radius:50%;background:#fff}
.nav-link{top:5px;font-size:2.4px;color:#fff}
.nav-cta{left:231px;top:3.9px;width:20px;height:4.6px;background:var(--red);color:#fff;font-size:2.4px;text-align:center;line-height:4.6px;border-radius:.6px}
/* hero */
.hero{left:0;top:14px;width:274px;height:105px;background:radial-gradient(ellipse at 42% 55%,#2c2c2c 0%,#0c0c0c 45%,var(--black) 75%)}
.hero-title{left:0;width:274px;top:45px;text-align:center;color:var(--blue);font-size:17px;font-weight:400}
.hero-sub{left:0;width:274px;top:67px;text-align:center;color:#fff;font-size:12px;font-weight:400}
/* crowd band */
.crowd{left:0;top:119px;width:274px;height:111px;background:linear-gradient(160deg,#cfd2d6 0%,#e6e7e9 40%,#d6d8db 70%,#eceded 100%)}
.tagline{left:51px;top:160px;width:172px;height:35px;background:var(--black);clip-path:polygon(3% 0,100% 0,97% 100%,0 100%);color:#fff;text-align:center;font-size:8.6px;line-height:12.8px;padding-top:4px}
.tagline b{color:var(--blue);font-weight:700}
/* photos */
.photo-van{left:27px;top:249px;width:221px;height:109px;background:linear-gradient(180deg,#b98a3c 0%,#d9d9d6 35%,#f2f2f0 60%,#8c8c8c 100%)}
.photo-room{left:26px;top:658px;width:222px;height:124px;background:linear-gradient(100deg,#9a9da0 0%,#d8d9da 30%,#5b6d7c 55%,#6e8c5a 80%,#c9cacb 100%)}
/* content */
.block-icon{left:41px;width:20px;height:20px}
.h-sec{left:68px;font-size:3.6px;color:var(--blue);font-weight:600;white-space:nowrap}
.h-sec .plain{color:var(--ink);font-weight:400}
.h-sec small{font-size:2.1px;color:var(--muted);font-weight:400;margin-left:1px}
.copy{left:68px;width:164px;font-size:2.15px;line-height:3.5px;color:#333;text-align:justify}
.copy p+p{margin-top:3.5px}
.copy b{font-weight:700;color:#111}
.feature{left:68px;width:140px}
.feature-title{font-size:2.6px;font-weight:700;color:#111;padding-left:6px;position:relative}
.feature-title::before{content:"";position:absolute;left:0;top:.3px;width:2.4px;height:2.4px;border-radius:50%;background:var(--blue)}
.feature-text{font-size:2.2px;line-height:3.4px;color:#444;padding-left:6px;margin-top:1px}
.feature-icon{left:205px;width:9px;height:9px}
.quote{left:80px;top:641px;width:115px;font-size:2.4px;line-height:3.6px;color:var(--navy);font-weight:700;text-align:center}
.qmark{font-size:12px;color:#c9c9c9;font-weight:700;top:636px}
/* about */
.about{left:0;top:807px;width:274px;height:166px;background:radial-gradient(ellipse at 85% 60%,#1d1d1d 0%,var(--black) 55%)}
.about-title{left:0;width:274px;top:825px;text-align:center;color:#fff;font-size:8.8px;font-weight:600}
.about-title span{color:var(--blue)}
.about-desc{left:46px;width:182px;top:838px;text-align:center;color:#fff;font-size:2.3px;line-height:3.3px;font-weight:600}
.cert-head{left:26px;top:853.5px;color:#fff;font-size:5.4px;font-weight:600}
.cert-rule{left:26px;top:863.5px;width:190px;height:.8px;background:var(--blue)}
.cert{left:26px;color:#fff;font-size:4.1px;display:flex;align-items:center;gap:4.5px}
.cert i{display:block;width:4px;height:4px;background:#fff}
.schedule{left:26px;top:917.5px;color:var(--blue);font-size:5.6px;font-weight:700}
.contact-bar{left:26.5px;top:928px;width:2px;height:28px;background:var(--blue)}
.contact{left:36px;color:#fff;font-size:3.6px;font-weight:600}
.contact.phone{color:var(--yellow);font-size:5.2px;font-weight:700}
.drone-art{left:148px;top:882px;width:75px;height:56px;background:radial-gradient(ellipse at center,#3a3a3a 0%,#171717 70%);border-radius:4px}
/* form */
.consult{left:0;top:973px;width:274px;height:179px;background:linear-gradient(90deg,#e9ecef 0%,#fbfbfc 30%,#f6f6f7 65%,#d9d4d4 85%,#b9b2b3 100%)}
.consult-title{left:0;width:274px;top:990px;text-align:center;font-size:9px;color:var(--navy);font-weight:500}
.consult-title span{color:var(--red);font-weight:600}
.field{height:11.5px;width:93px;background:#fff;border:.7px solid var(--field);border-radius:1.4px;font-size:2.6px;color:#9aa;padding:3.6px 3px}
.field.msg{width:196.5px;height:33px;padding-top:2px}
.btn{top:1118px;height:12px;border-radius:1.6px;color:#fff;font-size:5.4px;display:flex;align-items:center;justify-content:center;gap:2px}
.btn-download{left:38.5px;width:71px;background:var(--navy)}
.btn-submit{left:162px;width:72px;background:var(--red)}
.dl-ico{width:5.5px;height:5.5px}
/* footer */
.social{top:1170px;width:8px;height:8px;border-radius:50%;background:#2f6fb8}
.legal{left:0;width:274px;top:1184px;text-align:center;font-size:3px;color:#555;font-weight:600}
.bottom-bar{left:0;top:1196px;width:274px;height:4px;background:var(--navy)}
</style>
</head>
<body>
<div class="page">

  <header class="abs site-nav"></header>
  <div class="abs brand"><span class="brand-dot"></span>harrowfield</div>
  <span class="abs nav-link" style="left:138px">About Us</span>
  <span class="abs nav-link" style="left:163px">Services</span>
  <span class="abs nav-link" style="left:185px">Core Markets</span>
  <span class="abs nav-link" style="left:214px">Blog</span>
  <span class="abs nav-cta">Contact Us</span>

  <section class="abs hero"></section>
  <h1 class="abs hero-title">Field Anchor</h1>
  <h2 class="abs hero-sub">Special Event Services</h2>

  <div class="abs crowd" role="img" aria-label="Aerial photo of a large crowd gathered at an outdoor event"></div>
  <div class="abs tagline">Creating <b>SECURE</b> Environments<br>So You're In Control</div>

  <div class="abs photo-van" role="img" aria-label="Photo of the white Field Anchor command van parked outdoors"></div>

  <!-- special events -->
  <svg class="abs block-icon" style="top:384px" viewBox="0 0 20 20" fill="none" stroke="#555" stroke-width="1"><rect x="2" y="3" width="16" height="14" rx="1"/><line x1="2" y1="7" x2="18" y2="7"/><line x1="6" y1="1.5" x2="6" y2="4.5"/><line x1="14" y1="1.5" x2="14" y2="4.5"/><circle cx="10" cy="16" r="3" fill="#fff" stroke="#3a7fc0"/></svg>
  <div class="abs h-sec" style="top:380.5px">SPECIAL EVENTS<small>Pose Special Challenges</small></div>
  <div class="abs copy" style="top:387px"><p>Managing security is stressful under the best of circumstances, and planning for both the expected and the unexpected is part of the job. A special event adds crowds, tight schedules and shared spaces, so every threat must be weighed alongside the safety operations and technical infrastructure at your disposal.</p><p>How do you quickly and economically set up a mobile security operations center, equipped to gather and share information, coordinate personnel and manage operations and response teams? Harrowfield Consulting can help.</p></div>

  <!-- field anchor -->
  <svg class="abs block-icon" style="top:422px" viewBox="0 0 20 20" fill="none" stroke="#555" stroke-width="1"><path d="M2 15V8h11l4 3v4z" fill="#777"/><circle cx="6" cy="15.5" r="1.6" fill="#fff"/><circle cx="14" cy="15.5" r="1.6" fill="#fff"/><path d="M7 4a4 4 0 0 1 5 0M8 5.5a2 2 0 0 1 3 0" stroke="#3a7fc0"/></svg>
  <div class="abs h-sec" style="top:418px">HARROWFIELD'S FIELD ANCHOR<small>Special Event Services</small></div>
  <div class="abs copy" style="top:424.5px"><p>Harrowfield's Field Anchor and Special Event Services provide your event with the same level of technology you would expect in a permanent installation. Our vehicle carries a reliable, redundant set of surveillance, monitoring and communication systems, large screen monitors and a robust software platform that rivals traditional security operations centers. We also provide the staff and knowledge to deploy these systems, including site-wide placement of cameras, sensors, drones and supporting hardware.</p></div>

  <!-- support -->
  <svg class="abs block-icon" style="top:460px" viewBox="0 0 20 20" fill="none" stroke="#555" stroke-width="1.4"><path d="M4 8a7 7 0 1 0 3-3"/><path d="M10 2v3M13.5 3l-1 2.5" stroke="#3a7fc0"/></svg>
  <div class="abs h-sec" style="top:456px">SUPPORT <span class="plain">Services</span></div>
  <div class="abs copy" style="top:462.5px"><p>Professional Technical Staff: our knowledgeable technical staff make sure the technology aboard the vehicle is programmed and deployed for each event. Seasoned security professionals bring decades of experience as first responders, with deep knowledge of event planning, security operations and recovery.</p></div>

  <!-- capabilities -->
  <svg class="abs block-icon" style="top:488px" viewBox="0 0 20 20"><path d="M10 1l8 3v6c0 5-4 8-8 9-4-1-8-4-8-9V4z" fill="#666"/><circle cx="10" cy="9.5" r="4.2" fill="#fff"/><path d="M8 9.5l1.5 1.5 3-3" fill="none" stroke="#3a7fc0" stroke-width="1"/></svg>
  <div class="abs h-sec" style="top:488px">SPECIAL EVENTS<small>Pose Special Challenges</small></div>

  <div class="abs feature" style="top:495.5px"><div class="feature-title">RAPID VIDEO SYSTEM DEPLOYMENT</div><div class="feature-text">Our cameras are designed to be deployed anywhere, even without power or Ethernet.</div></div>
  <div class="abs feature" style="top:510.5px"><div class="feature-title">AERIAL DRONE SURVEILLANCE</div><div class="feature-text">Equipped with high resolution cameras and thermal imaging capabilities, our drones provide a visual perspective that enhances overall situational awareness and supports damage</div></div>
  <div class="abs feature" style="top:528px"><div class="feature-title">DRONE DETECTION TECHNOLOGY</div><div class="feature-text">State-of-the-art drone detection technologies detect drone activity, pilot location, and classify the drone's characteristics</div></div>
  <div class="abs feature" style="top:545.5px"><div class="feature-title">GUNFIRE DETECTION</div><div class="feature-text">Our technology positively identifies gunfire, providing law enforcement and first responders with critical</div></div>
  <div class="abs feature" style="top:563px"><div class="feature-title">REAL-TIME WEATHER MONITORING</div><div class="feature-text">Our field anchor vehicle has live reporting curated remotely by a dedicated meteorologist.</div></div>
  <div class="abs feature" style="top:580.5px"><div class="feature-title">SOCIAL MEDIA MONITORING</div><div class="feature-text">Equipped to monitor various social media platforms, we use real-time intel to detect threats based on key words, sentiment, subject matter and geo-location.</div></div>

  <svg class="abs feature-icon" style="top:495px" viewBox="0 0 10 10" fill="none" stroke="#2b4f86" stroke-width=".7"><rect x="1" y="2" width="6" height="3.5" rx=".6"/><path d="M7 3l2-1v4l-2-1M3 5.5v3H1"/></svg>
  <svg class="abs feature-icon" style="top:513px" viewBox="0 0 10 10" fill="none" stroke="#2b4f86" stroke-width=".7"><rect x="3" y="4" width="4" height="3"/><path d="M1 3h3M6 3h3M2.5 3v1.5M7.5 3v1.5"/></svg>
  <svg class="abs feature-icon" style="top:530px" viewBox="0 0 10 10" fill="none" stroke="#2b4f86" stroke-width=".7"><path d="M4 1v8M6 2v7M2 4l2-1M8 4L6 3"/></svg>
  <svg class="abs feature-icon" style="top:548px" viewBox="0 0 10 10" fill="none" stroke="#2b4f86" stroke-width=".7"><path d="M1 9l7-7M7 1l2 2M2 7l1 1"/></svg>
  <svg class="abs feature-icon" style="top:566px" viewBox="0 0 10 10" fill="none" stroke="#2b4f86" stroke-width=".7"><circle cx="5" cy="5" r="2"/><path d="M5 1v1M5 8v1M1 5h1M8 5h1M2.2 2.2l.7.7M7.1 7.1l.7.7M7.8 2.2l-.7.7"/></svg>
  <svg class="abs feature-icon" style="top:583px" viewBox="0 0 10 10" fill="none" stroke="#2b4f86" stroke-width=".7"><rect x="1" y="1.5" width="8" height="5.5" rx=".5"/><path d="M3.5 9h3M5 7v2"/></svg>

  <!-- communication -->
  <svg class="abs block-icon" style="top:602px" viewBox="0 0 20 20" fill="#666"><circle cx="10" cy="5" r="2.6"/><circle cx="4" cy="15" r="2.6"/><circle cx="16" cy="15" r="2.6"/><path d="M10 5L4 15M10 5l6 10M4 15h12" stroke="#666" stroke-width=".8"/></svg>
  <div class="abs h-sec" style="top:603px">COMMUNICATION <span class="plain">Systems</span></div>
  <div class="abs copy" style="top:609.5px"><p><b>Landline Telephone Service</b> – Crisp, clear communications with landline handsets over cellular or satellite ensures intelligible audio.</p><p><b>Two-Way Radios and Cellular PTT Radios</b> – Our two-way radios can be programmed to our clients' operating frequencies to expand their current radio communications into the vehicle. Our cellular PTT radios extend communications reach.</p><p><b>Satellite TV, Radio &amp; Cellular Data</b> – The vehicle keeps continuous, high-speed, reliable data communications, coupled with live satellite TV and radio to maximize access to inbound information.</p></div>

  <span class="abs qmark" style="left:78px">“</span>
  <span class="abs qmark" style="left:187px;top:637px">”</span>
  <div class="abs quote">Trust Harrowfield's Field Anchor and Special Event Services<br>to keep your next special event safe, secure, and “uneventful.”</div>

  <div class="abs photo-room" role="img" aria-label="Photo of the command vehicle interior with workstations, chairs and wall screens showing a site map"></div>

  <!-- about -->
  <section class="abs about"></section>
  <h2 class="abs about-title">About <span>Harrowfield Consulting</span></h2>
  <p class="abs about-desc">Harrowfield Consulting is a team of seasoned security professionals with backgrounds in security management, law enforcement, emergency services and security technology. Put our expertise and experience to work for you!</p>
  <div class="abs cert-head">Harrowfield employees hold various certifications and licenses, including:</div>
  <div class="abs cert-rule"></div>
  <div class="abs cert" style="top:869px"><i></i>CPP – Certified Protection Professional</div>
  <div class="abs cert" style="top:878.5px"><i></i>CPOI – Certified Protection Officer Instructor</div>
  <div class="abs cert" style="top:888px"><i></i>FAA Part 107 – Certified Drone Pilot</div>
  <div class="abs cert" style="top:897px"><i></i>PSP – Physical Security Professional</div>
  <div class="abs cert" style="top:906.5px"><i></i>P.E. - Professional Engineer</div>
  <div class="abs drone-art" role="img" aria-label="Line illustration of a camera drone"></div>
  <div class="abs schedule">SCHEDULE A FREE CONSULTATION:</div>
  <div class="abs contact-bar"></div>
  <div class="abs contact phone" style="top:930px">888.555.0147</div>
  <div class="abs contact" style="top:938px">www.harrowfield.us</div>
  <div class="abs contact" style="top:945.5px">Harrowfield Consulting, One Calder Plaza,</div>
  <div class="abs contact" style="top:952px">12th Floor, Easton, New York 10990</div>

  <!-- consultation form -->
  <section class="abs consult" role="img" aria-label="Faded photo of the command van behind the request form"></section>
  <h2 class="abs consult-title">Request a <span>Free Consultation</span></h2>
  <div class="abs field" style="left:38.5px;top:1010px">Name*</div>
  <div class="abs field" style="left:141.5px;top:1010px">Company*</div>
  <div class="abs field" style="left:38.5px;top:1031px">City*</div>
  <div class="abs field" style="left:141.5px;top:1031px">State*</div>
  <div class="abs field" style="left:38.5px;top:1053px">Phone*</div>
  <div class="abs field" style="left:141.5px;top:1053px">Email*</div>
  <div class="abs field msg" style="left:38.5px;top:1075px">Message</div>
  <div class="abs btn btn-download"><svg class="dl-ico" viewBox="0 0 6 6" fill="none" stroke="#fff" stroke-width=".5"><rect x=".5" y=".5" width="5" height="5" rx=".6"/><path d="M3 1.5v2.5M2 3l1 1 1-1"/></svg>Download Brochure</div>
  <div class="abs btn btn-submit">SUBMIT</div>

  <!-- footer -->
  <span class="abs social" style="left:128px"></span>
  <span class="abs social" style="left:138.5px"></span>
  <p class="abs legal">Privacy Policy | © 2020 Harrowfield Consulting. All Rights Reserved. Web Design by BrightPane Studio.</p>
  <div class="abs bottom-bar"></div>
</div>
</body>
</html>
```